Business Card Design Project

We are a construction company in Orange County, CA. We need a two sided business card. We would like the back to be our logo with web URL. Front should included Name, title, address, phone, fax and email address.

our address is
627 West Dorrance Blvd, Suite 308
Anaheim, CA 92718

Our logo files are attached.

Construction

```html
<!DOCTYPE html>
<html lang="en">
<head>
<meta charset="utf-8">
<title>Halden Business Card</title>
<link rel="stylesheet" href="https://fonts.googleapis.com/css2?family=Open+Sans:wght@400;700;800&display=swap">
<style>
  :root {
    --brand-blue: #1b4a7c;
    --text-grey: #4a4a4a;
    --card-white: #ffffff;
    --backdrop: #e9e6e2;
    --rule: #b9b9b9;
  }
  * { margin: 0; padding: 0; box-sizing: border-box; }
  html, body {
    width: 1200px; height: 1094px; overflow: hidden;
    background: var(--backdrop);
    font-family: "Open Sans", Arial, sans-serif;
  }
  .card {
    position: absolute;
    width: 764px; height: 436px;
    background: var(--card-white);
    box-shadow: 0 2px 6px rgba(0,0,0,0.18);
    overflow: hidden;
  }
  .card--front { left: 70px; top: 83px; }
  .card--back { left: 340px; top: 564px; }

  .holder {
    position: absolute; top: 26px; left: 0; width: 764px;
    text-align: center; color: var(--brand-blue);
    font-size: 26px; line-height: 36px; font-weight: 400;
  }
  .holder strong { font-weight: 700; }

  .company-name {
    position: absolute; left: 0; width: 764px;
    text-align: center; color: var(--brand-blue);
    font-weight: 800; font-size: 104px; line-height: 1;
    letter-spacing: -2px;
  }
  .card--front .company-name { top: 92px; }
  .card--back .company-name { top: 117px; }

  .address {
    position: absolute; right: 416px; top: 285px;
    text-align: right; color: var(--text-grey);
    font-style: normal; font-size: 18px; line-height: 24.5px;
    white-space: nowrap;
  }
  .divider {
    position: absolute; left: 374px; top: 272px;
    width: 1px; height: 105px; background: var(--rule);
  }
  .contacts {
    position: absolute; left: 390px; top: 270px;
    list-style: none; color: var(--text-grey);
    font-size: 18px; line-height: 24.5px;
    white-space: nowrap;
  }
  .contacts li { display: flex; align-items: center; gap: 9px; }
  .contacts svg { width: 14px; height: 14px; fill: var(--text-grey); flex: none; }

  .band {
    position: absolute; left: 0; bottom: 0; width: 764px; height: 16px;
  }

  .web-address {
    position: absolute; top: 276px; left: 0; width: 764px;
    text-align: center; color: var(--text-grey);
    font-size: 20px; line-height: 30px; letter-spacing: 4px;
  }
</style>
</head>
<body>

<section class="card card--front">
  <p class="holder"><strong>Your Name,</strong> Title</p>
  <p class="company-name">HALDEN</p>

  <address class="address">
    627 West Dorrance Blvd<br>
    Suite 308, Anaheim<br>
    CA&nbsp; 92718
  </address>

  <div class="divider"></div>

  <ul class="contacts">
    <li>
      <svg viewBox="0 0 16 16" aria-hidden="true"><path d="M3.6 1.2l2.3 2.9-1.4 1.7c.9 2 2.6 3.7 4.7 4.7l1.7-1.4 2.9 2.3-1.4 2.7C7 13.8 2.2 9 1 2.6z"/></svg>
      01-555-0142
    </li>
    <li>
      <svg viewBox="0 0 16 16" aria-hidden="true"><path d="M4 1h6v4H4zM2 6h12v6h-2v3H4v-3H2zm3 6v2h6v-2z"/></svg>
      01-555-0143
    </li>
    <li>
      <svg viewBox="0 0 16 16" aria-hidden="true"><path d="M1 3h14v10H1zm1 1l6 5 6-5z"/></svg>
      info@haldenbuild.com
    </li>
    <li>
      <svg viewBox="0 0 16 16" aria-hidden="true"><circle cx="8" cy="8" r="7"/><path d="M1 8h14M8 1v14" stroke="#fff" stroke-width="1"/></svg>
      www.haldenbuild.com
    </li>
  </ul>

  <svg class="band" viewBox="0 0 764 16" aria-hidden="true">
    <rect width="764" height="16" fill="var(--brand-blue)"/>
    <polygon points="462,0 480,0 462,16 444,16" fill="var(--card-white)"/>
  </svg>
</section>

<section class="card card--back">
  <p class="company-name">HALDEN</p>
  <p class="web-address">www.haldenbuild.com</p>
</section>

</body>
</html>
```